Website for Dental Office - The Bright Arch Clinic

The bright arch clinic is a dental office offering cosmetic dentistry, general dentistry, and multi-specialty dental care all under one roof in our state-of-the-art cosmetic dental center. We are particularly striving to provide services that fit the need of the young generation. Thus, we hope to have a modern, professional concise website that represents our spirit.

*Should be able to switch from English to Chinese

6 sections besides homepage:
Home, Meet us, Services,
Patient Info, Cases&Reviews, Blog, Contact

The Services sections should contain multiple subsections such as cleaning and prevention, cosmetic dentistry, implant dentistry, removable dentures, etc...
The Patient Info section is also intended to contain several subsections such as
New Patient offer, accepted Insurance, patient portal, helpful tips, etc...

Target Market(s)

young generation

Coding

Coded - Design and coding required

Number of Pages Required

5+ page

Font styles to use
Sans Serif

Colors
0592cd
33a6d7
85cae6
00a990
33b8a4
86cfc6
cee9f5
cfeae6
3277b5

Requirements
Must have
• *Should be able to switch from English to Chinese
Nice to have
• http://www.thebrightarchclinic.com/
• As a reference, the above link is the current website, but we would like to change the appearance and the content (our new logo's picture is attached)

```html
<!DOCTYPE html>
<html lang="en">
<head>
<meta charset="utf-8">
<title>Cleaning and Prevention – The Bright Arch Clinic</title>
<link href="https://fonts.googleapis.com/css2?family=Montserrat:wght@400;500;600;700;800&display=swap" rel="stylesheet">
<style>
:root{
  --blue:#0592cd;--blue-2:#33a6d7;--blue-3:#85cae6;--blue-pale:#cee9f5;
  --teal:#00a990;--teal-2:#33b8a4;--teal-3:#86cfc6;--teal-pale:#cfeae6;
  --navy:#3277b5;--ink:#1c1c1c;--text:#6b6b6b;--grey-bg:#efefef;--white:#fff;
}
*{margin:0;padding:0;box-sizing:border-box}
html,body{width:1200px;height:4713px;overflow:hidden}
body{font-family:'Montserrat',sans-serif;color:var(--text);background:var(--white);position:relative}
.page{position:relative;width:1200px;height:4713px;overflow:hidden}
.abs{position:absolute}
.photo{position:absolute;border-radius:50%}
p{font-size:11px;line-height:19.5px}

.top-band{left:0;top:0;width:1200px;height:300px}
.site-header{left:0;top:0;width:1200px;height:100px;border-top:3px solid var(--blue)}
.brand{left:161px;top:22px;display:flex;align-items:center;gap:12px}
.brand-mark{width:34px;height:34px;background:var(--blue-2);border-radius:4px}
.brand-name{font-weight:700;font-size:19px;color:var(--blue-2);line-height:22px;width:170px}
.main-nav{left:396px;top:38px;display:flex;gap:19px;font-size:10.5px;font-weight:500;color:#333}
.main-nav .active{color:var(--teal)}
.phone-badge{left:865px;top:-12px;width:110px;height:110px;border-radius:50%;background:var(--navy);color:#fff;text-align:center;padding-top:40px;font-weight:700;font-size:12px}
.phone-badge svg{display:block;margin:0 auto 7px}
.lang-switch{left:988px;top:30px;width:51px;height:28px;border-radius:3px;background:var(--teal);color:#fff;font-size:10px;line-height:28px;text-align:center}

h1.page-title{left:0;top:216px;width:1200px;text-align:center;font-weight:700;font-size:40px;letter-spacing:1px;color:var(--ink)}
.lead{left:330px;top:280px;width:540px;text-align:center;font-size:11px;line-height:20px}
h2.sub{font-weight:700;font-size:24px;color:var(--ink)}
.blue-text{color:var(--blue)}
.check-list{list-style:none;font-size:11px}
.check-list li{position:relative;padding-left:18px;height:30px;line-height:14px}
.check-list li::before{content:"";position:absolute;left:0;top:1px;width:9px;height:9px;border:1.5px solid var(--blue-2);border-radius:50%}
.chip{height:53px;width:196px;background:#fff;box-shadow:0 2px 10px rgba(0,0,0,.08);border:1px solid #eef5f8;color:var(--teal);font-size:11px;font-weight:600;text-align:center;line-height:53px}

.xray-band{left:0;top:960px;width:1200px;height:958px}
.tile{width:196px;height:88px;background:#fff;box-shadow:0 2px 10px rgba(0,0,0,.06);color:var(--teal);font-weight:600;font-size:11px;line-height:22px;padding:22px 16px}
.tile.lead-tile{background:var(--navy);color:#fff}

.center-title{left:0;width:1200px;text-align:center;font-weight:700;color:var(--ink)}
.reason{width:270px;height:209px;color:#fff;text-align:center;padding:38px 14px 0}
.reason .icon{width:36px;height:36px;margin:0 auto 16px;border:2px solid #fff;border-radius:50%}
.reason h3{font-size:14px;font-weight:700;margin-bottom:4px}
.reason p{font-size:10.5px;line-height:20px}

.fluoride-band{left:0;top:2528px;width:1200px;height:314px}
.fluoride-band h2{font-weight:700;font-size:40px;color:#fff;letter-spacing:1px}

.night-band{left:0;top:3120px;width:1200px;height:560px}
.big-title{font-weight:700;font-size:40px;color:var(--ink);letter-spacing:.5px}

.care-card{width:196px;height:191px;background:#fff;box-shadow:0 2px 12px rgba(0,0,0,.08);padding:18px 14px}
.care-card .icon{width:34px;height:34px;border:2px solid var(--blue);border-radius:50%;margin-bottom:10px}
.care-card h3{font-size:12px;font-weight:700;color:var(--ink);margin-bottom:6px}
.care-card p{font-size:10px;line-height:19px}

.footer-bg{left:0;top:4335px;width:1200px;height:352px;background:var(--grey-bg)}
.cta{left:161px;top:4262px;width:876px;height:164px}
.cta small{position:absolute;left:22px;top:64px;color:#fff;font-size:11px}
.cta strong{position:absolute;left:22px;top:84px;color:#fff;font-size:32px;font-weight:700;letter-spacing:1px}
.cta .btn{position:absolute;left:622px;top:82px;width:225px;height:40px;border-radius:20px;background:#fff;color:var(--ink);font-size:11px;font-weight:700;text-align:center;line-height:40px}
.foot-col h4{font-size:11px;font-weight:700;color:#222;margin-bottom:16px;letter-spacing:.5px}
.foot-col li{list-style:none;font-size:10.5px;line-height:19px;color:#666}
.hours td{font-size:10.5px;line-height:19px;color:#666;padding-right:14px}
.hours td b{color:#333}
.social{width:34px;height:34px;border-radius:50%;background:var(--blue)}
.bottom-bar{left:0;top:4687px;width:1200px;height:26px;background:#e4e4e4;font-size:10px;line-height:26px;padding:0 161px;display:flex;justify-content:space-between}
.bottom-bar span.accent{color:var(--teal)}
</style>
</head>
<body>
<div class="page">

<svg class="abs top-band" viewBox="0 0 1200 300" preserveAspectRatio="none" aria-hidden="true">
  <defs><linearGradient id="skyfade" x1="0" y1="0" x2="0" y2="1"><stop offset="0" stop-color="#cbeaf8"/><stop offset="1" stop-color="#ffffff"/></linearGradient></defs>
  <path d="M0 60 Q600 210 1200 60 L1200 0 L0 0Z" fill="#fff"/>
  <path d="M0 60 Q600 210 1200 60 L1200 300 L0 300Z" fill="url(#skyfade)"/>
</svg>

<header class="abs site-header">
  <a class="abs brand"><span class="brand-mark"></span><span class="brand-name">The Bright Arch Clinic</span></a>
  <nav class="abs main-nav"><span>HOME</span><span>MEET US</span><span class="active">SERVICES</span><span>PATIENT INFO</span><span>REVIEWS</span><span>BLOG</span><span>CONTACT</span></nav>
  <div class="abs phone-badge"><svg width="18" height="18" viewBox="0 0 24 24"><path fill="#fff" d="M6.6 10.8a15 15 0 006.6 6.6l2.2-2.2a1 1 0 011-.25 11.4 11.4 0 003.6.57 1 1 0 011 1V20a1 1 0 01-1 1A17 17 0 013 4a1 1 0 011-1h3.5a1 1 0 011 1c0 1.25.2 2.45.57 3.57a1 1 0 01-.25 1z"/></svg>555.014.2736</div>
  <div class="abs lang-switch">汉语 ▾</div>
</header>

<h1 class="abs page-title">CLEANING AND PREVENTION</h1>
<p class="abs lead">Lorem Ipsum is dummy text of the printing and typesetting industry. Lorem Ipsum has been the industry's standard dummy text.</p>

<h2 class="abs sub" style="left:161px;top:410px">Dental Exams</h2>
<p class="abs blue-text" style="left:161px;top:456px;width:380px;font-size:11px">Your dentist will perform a comprehensive dental and oral health exam at your initial visit. This will include:</p>
<ul class="abs check-list" style="left:161px;top:518px">
  <li>Examination of diagnostic radiographs (x-rays)</li><li>Oral cancer screening</li><li>Gum disease evaluation</li><li>Examination of tooth decay</li><li>Examination of existing restorations</li>
</ul>
<div class="photo" style="left:622px;top:339px;width:164px;height:164px;background:var(--teal)"></div>
<div class="photo" role="img" aria-label="Patient in the dental chair during an exam" style="left:662px;top:352px;width:376px;height:376px;background:radial-gradient(circle at 40% 40%,#f1d2c3,#9fbfd8)"></div>
<div class="photo" style="left:909px;top:626px;width:120px;height:120px;border:2px solid var(--blue-2)"></div>
<div class="photo" style="left:906px;top:708px;width:58px;height:58px;background:var(--navy)"></div>

<h2 class="abs sub" style="left:161px;top:720px">Professional Dental Cleaning:</h2>
<p class="abs" style="left:161px;top:764px;width:450px">Professional dental cleanings (oral prophylaxis) are usually performed by the dentist or a registered dental hygienist. Your cleaning appointment will include a dental exam and the following:</p>
<div class="abs chip" style="left:161px;top:852px">Removal of calculus (tartar)</div>
<div class="abs chip" style="left:380px;top:852px">Removal of plaque</div>
<div class="abs chip" style="left:600px;top:852px">Teeth polishing</div>

<svg class="abs xray-band" viewBox="0 0 1200 958" preserveAspectRatio="none" aria-hidden="true">
  <path d="M0 20 C200 -10 330 70 520 100 C760 130 900 20 1200 40 L1200 958 L0 958Z" fill="#85cae6" opacity=".6"/>
  <path d="M0 60 C250 40 400 140 620 110 C820 80 980 50 1200 70 L1200 958 L0 958Z" fill="#d2edf3"/>
</svg>
<div class="photo" role="img" aria-label="Panoramic dental x-ray" style="left:214px;top:1172px;width:300px;height:300px;border:4px solid #fff;background:radial-gradient(circle,#9ed0a8,#2f6e75)"></div>
<h2 class="abs big-title" style="left:572px;top:1214px;font-size:38px">Dental X-Rays</h2>
<p class="abs" style="left:572px;top:1276px;width:384px">Dental radiographs (x-rays) are essential, preventative, diagnostic tools that provide valuable information not visible during a regular dental exam. Dentists and dental hygienists use this information to safely and accurately detect hidden dental abnormalities and complete an accurate treatment plan. Detecting and treating dental problems at an early stage can save you time, money, unnecessary discomfort and your teeth!</p>
<div class="abs tile lead-tile" style="left:161px;top:1509px">Dental x-rays may reveal:</div>
<div class="abs tile" style="left:388px;top:1509px">Abscesses or cysts</div>
<div class="abs tile" style="left:616px;top:1509px">Bone loss</div>
<div class="abs tile" style="left:843px;top:1509px">Cancerous and non-cancerous tumors</div>
<div class="abs tile" style="left:161px;top:1630px">Decay between the teeth</div>
<div class="abs tile" style="left:388px;top:1630px">Developmental abnormalities</div>
<div class="abs tile" style="left:616px;top:1630px">Poor tooth and root positions</div>
<div class="abs tile" style="left:843px;top:1630px">Problems inside a tooth or below the gum line</div>
<p class="abs" style="left:161px;top:1768px;width:878px">A full mouth series or a panoramic view of dental x-rays is recommended for new patients. A full series is usually good for two to five years. Bite-wing x-rays (x-rays of top and bottom teeth biting together) are taken at recall (check-up) visits and are recommended once or twice a year to detect any new dental problems.</p>

<h2 class="abs center-title" style="top:1998px;font-size:40px">SEALANTS</h2>
<p class="abs" style="left:160px;top:2054px;width:880px;text-align:center">A sealant is a thin, composite coating applied to the chewing surface of molars, premolars and any deep grooves (called pits and fissures) of teeth. Most dental decay begins in these deep grooves. Teeth with these conditions are hard to clean and are very susceptible to decay. A sealant protects the tooth by sealing deep grooves, creating a smooth, easy to clean surface. Sealants can protect teeth from decay for many years, but need to be checked for wear and chipping at regular dental visits.</p>
<h3 class="abs center-title" style="top:2166px;font-size:22px;font-weight:600">Reasons for sealants:</h3>
<div class="abs reason" style="left:161px;top:2220px;background:var(--blue-2)"><div class="icon" role="img" aria-label="Child icon"></div><h3>Children and teenagers</h3><p>As soon as the six-year molars (the first permanent back teeth) appear or any time throughout the cavity prone years of 6-16.</p></div>
<div class="abs reason" style="left:465px;top:2220px;background:var(--teal)"><div class="icon" role="img" aria-label="Adult icon"></div><h3>Adults</h3><p>Tooth surfaces without decay that have deep grooves or depressions.</p></div>
<div class="abs reason" style="left:768px;top:2220px;background:#33b5cf"><div class="icon" role="img" aria-label="Baby icon"></div><h3>Baby teeth</h3><p>Occasionally done if teeth have deep grooves or depressions and child is cavity prone.</p></div>

<svg class="abs fluoride-band" viewBox="0 0 1200 314" preserveAspectRatio="none" aria-hidden="true">
  <path d="M0 0 L790 0 C880 0 880 140 760 250 C720 290 690 314 640 314 L0 314Z" fill="#0592cd"/>
</svg>
<div class="photo" role="img" aria-label="Girl receiving fluoride treatment with a curing light" style="left:733px;top:2508px;width:305px;height:305px;border:4px solid #fff;background:radial-gradient(circle at 60% 50%,#f0d3c0,#7fb3d6)"></div>
<div class="abs fluoride-band">
  <h2 class="abs" style="left:161px;top:46px">FLORIDE TREATMENT</h2>
  <p class="abs" style="left:161px;top:110px;width:500px;color:#fff">Fluoride is one of the most effective agents available to help prevent tooth decay. It is a mineral that is naturally present in varying amounts in almost all foods and water supplies. The benefits of fluoride have been well known for over 50 years and are supported by many health and professional organizations.</p>
  <p class="abs" style="left:161px;top:208px;width:500px;color:#fff">Although most people receive fluoride from food and water, sometimes it is not enough to help prevent decay. Your dentist or dental hygienist may recommend the use of home and/or professional fluoride treatments for the following reasons:</p>
</div>
<ul class="abs check-list" style="left:161px;top:2892px">
  <li>Deep pits and fissures on the chewing surfaces of teeth</li><li>Exposed and sensitive root surfaces</li><li>Fair to poor oral hygiene habits</li><li>Frequent sugar and carbohydrate intake</li><li>Inadequate exposure to fluorides</li>
</ul>
<ul class="abs check-list" style="left:600px;top:2882px;width:420px">
  <li style="height:50px;line-height:19px">Inadequate saliva flow due to medical conditions, medical treatments or medications</li><li>Recent history of dental decay</li><li>To help prevent dental caries under existing dental restorations</li>
</ul>
<p class="abs" style="left:161px;top:3060px;color:#111;font-weight:600">Remember, fluoride alone will not prevent tooth decay!</p>
<p class="abs" style="left:161px;top:3080px;color:var(--teal)">It is important to brush at least twice a day, floss regularly, eat balanced meals, reduce sugary and acidic snacks, and visit your dentist on a regular basis.</p>

<svg class="abs night-band" viewBox="0 0 1200 560" preserveAspectRatio="none" aria-hidden="true">
  <defs><linearGradient id="nightfade" x1="0" y1="0" x2="0" y2="1"><stop offset="0" stop-color="#cdeaf7"/><stop offset="1" stop-color="#ffffff"/></linearGradient></defs>
  <path d="M0 40 Q600 -40 1200 40 L1200 560 L0 560Z" fill="url(#nightfade)"/>
</svg>
<div class="photo" role="img" aria-label="Smiling young woman" style="left:170px;top:3265px;width:300px;height:300px;background:radial-gradient(circle at 55% 45%,#f3dccd,#6a4a3a)"></div>
<div class="photo" style="left:377px;top:3460px;width:110px;height:110px;background:var(--teal)"></div>
<div class="photo" style="left:494px;top:3472px;width:36px;height:36px;background:var(--blue-2)"></div>
<div class="photo" style="left:498px;top:3525px;width:14px;height:14px;background:var(--navy)"></div>
<h2 class="abs big-title" style="left:572px;top:3305px">NIGHT GUARDS</h2>
<p class="abs" style="left:572px;top:3366px;width:468px">The pain and discomfort of Bruxism, the grinding of your teeth while sleep, is shared by millions of people. The costs in pain, headaches, TMJ problems and tooth damage/sensitivity are usually too much to bear.</p>
<p class="abs" style="left:572px;top:3443px;width:468px">A Night Guard is a simple, affordable solution for protecting your teeth and jaw from the detrimental effects of nighttime teeth grinding. It consists of an acrylic tray that comfortably fits over your upper teeth. This creates a cushion between the upper and lower teeth and absorbs the force of grinding.</p>
<p class="abs blue-text" style="left:572px;top:3541px;font-weight:500">Ask your dentist how you can obtain your own custom-made night guard !!</p>

<h2 class="abs big-title" style="left:161px;top:3692px">HOME CARE</h2>
<p class="abs" style="left:161px;top:3752px;width:375px">A beautiful, healthy smile that lasts a lifetime is our ultimate goal when treating patients. Your personal home care plays an important role in achieving that goal. It starts at home by eating balanced meals, reducing the number of snacks you eat, and correctly using the various dental aids that help control the plaque and bacteria that cause dental disease.</p>
<div class="abs care-card" style="left:161px;top:3899px"><div class="icon" role="img" aria-label="Tooth icon"></div><h3>Tooth brushing</h3><p>Brush your teeth at least twice a day (especially before going to bed at night) with a dentist-approved toothbrush and toothpaste.</p></div>
<div class="abs care-card" style="left:388px;top:3899px"><div class="icon" role="img" aria-label="Floss icon"></div><h3>Flossing</h3><p>Daily flossing is the best way to clean between the teeth and under the gumline. Flossing not only helps clean these spaces, it disrupts plaque colonies.</p></div>
<div class="photo" role="img" aria-label="Little girl brushing her teeth" style="left:693px;top:3700px;width:348px;height:348px;border:3px solid var(--teal);background:radial-gradient(circle at 50% 40%,#f4dcc8,#b8d86a)"></div>
<div class="photo" style="left:683px;top:3898px;width:164px;height:164px;border:2px solid var(--blue-2)"></div>
<div class="photo" style="left:675px;top:4028px;width:58px;height:58px;background:var(--navy)"></div>
<p class="abs" style="left:161px;top:4133px;width:880px">Using other dental aids such as interdental brushes, electric toothbrushes, rubber tip stimulators, tongue cleaners, irrigation devices, fluoride, medicated rinses, etc., recommended by your dentist or dental hygienist can also play a vital role in good dental home care.</p>

<div class="abs footer-bg"></div>
<div class="abs cta">
  <svg class="abs" style="left:0;top:0" width="876" height="164" viewBox="0 0 876 164" aria-hidden="true">
    <defs><linearGradient id="ctafade" x1="0" y1="0" x2="1" y2="0"><stop offset="0" stop-color="#0592cd"/><stop offset="1" stop-color="#00a990"/></linearGradient></defs>
    <path d="M0 0 L876 34 L876 158 Q876 164 870 164 L6 164 Q0 164 0 158Z" fill="url(#ctafade)"/>
  </svg>
  <small>Lorem Ipsum is dummy text of the printing and typesetting.</small>
  <strong>YOUR SMILE. OUR PASSION.</strong>
  <span class="btn">BOOK AN APPOINTMENT</span>
</div>

<div class="abs" style="left:161px;top:4476px;width:196px;text-align:center">
  <span style="display:block;width:60px;height:60px;margin:0 auto 12px;background:var(--blue-2);border-radius:4px"></span>
  <span style="font-weight:700;font-size:17px;color:var(--blue-2)">The Bright Arch Clinic</span>
</div>
<div class="abs" style="left:179px;top:4625px;display:flex;gap:8px">
  <span class="social"></span><span class="social"></span><span class="social" style="background:var(--teal)"></span><span class="social" style="background:var(--teal-2)"></span>
</div>

<div class="abs foot-col" style="left:390px;top:4470px">
  <h4>USEFUL LINKS</h4>
  <ul><li>Home</li><li>Meet Us</li><li>Services</li><li>Patient Info</li><li>Case &amp; Reviews</li><li>Blog</li><li>Contact</li></ul>
</div>
<div class="abs foot-col" style="left:616px;top:4470px">
  <h4>OPENING HOURS</h4>
  <table class="hours">
    <tr><td>Sunday &amp; Monday</td><td><b>Closed</b></td></tr>
    <tr><td>Tuesday</td><td><b>9:30AM – 5:00PM</b></td></tr>
    <tr><td>Wednesday</td><td><b>Closed</b></td></tr>
    <tr><td>Thursday</td><td><b>9:30AM – 5:00PM</b></td></tr>
    <tr><td>Friday</td><td><b>9:00AM – 5:00PM</b></td></tr>
    <tr><td>Saturday</td><td><b>9:00AM – 5:00PM</b></td></tr>
  </table>
</div>
<div class="abs foot-col" style="left:845px;top:4470px;width:200px">
  <h4>CONTACT INFO</h4>
  <div style="display:flex;gap:10px;font-size:10.5px;line-height:19px"><svg width="12" height="16" viewBox="0 0 12 16"><path fill="#00a990" d="M6 0a6 6 0 00-6 6c0 4.5 6 10 6 10s6-5.5 6-10a6 6 0 00-6-6zm0 8.3A2.3 2.3 0 116 3.7a2.3 2.3 0 010 4.6z"/></svg><span>27 Harbor Lane, Suite 210,<br>Easton MA 02100</span></div>
  <div style="display:flex;gap:10px;margin-top:14px;font-size:14px;color:#333;font-weight:500"><svg width="14" height="14" viewBox="0 0 24 24"><path fill="#3277b5" d="M6.6 10.8a15 15 0 006.6 6.6l2.2-2.2a1 1 0 011-.25 11.4 11.4 0 003.6.57 1 1 0 011 1V20a1 1 0 01-1 1A17 17 0 013 4a1 1 0 011-1h3.5a1 1 0 011 1c0 1.25.2 2.45.57 3.57a1 1 0 01-.25 1z"/></svg>555.014.2736</div>
  <div style="display:flex;gap:10px;margin-top:18px;font-size:10.5px"><svg width="14" height="11" viewBox="0 0 14 11"><rect width="14" height="11" rx="1" fill="#33a6d7"/><path d="M1 1l6 5 6-5" stroke="#fff" fill="none"/></svg>info@thebrightarchclinic.com</div>
</div>

<div class="abs bottom-bar"><span><span class="accent">© The Bright Arch Clinic</span> – 2019. All Rights Reserved.</span><span class="accent">Easton Cosmetic Care</span></div>

</div>
</body>
</html>
```